Business Card Design Project : Ridgeline Press

In preparation for market launch, Tamarind's Ridgeline Press require the development of a business card. Ridgeline Press is a Community online publishing web portal. We provide the the city of Whistler located in B.C. (Canada) business directories, News, Classified ads, News, Events and blogs etc.

The main focus of the brand is to help local businesses to corporate with their online advertisement and marketing. Meeting our clients face to face is a must (B2B).

Target Market(s)

The target market is B2B customers. Business Owners to Marketing, advertising Managers

Industry/Entity Type

Business

Requirements
Must have
• - The business card will be two sided.
the BACK side will have our logo which consist of (icon, url,slogan) submited. The logo will be middle and centred.

The FRONT side should have company details:

Company Legal Name: TAMARIND RIDGELINE MEDIA

Owen Farsk
Director of Sales & Marketing

www.tamarindridgeline.biz
owen@tamarindridgeline.biz

Phone: 604 317 8842
#2714 - 582 E. Halvern St.
Vancouver, B.C. V7K2R4 Canada
Nice to have
• - For the "FRONT" side of our business card. You can separate or re-arrange with our logo components (icon, logo,slogan). It does not have to be together.

Also our company legal name is rather long so arrange or organize the name in a way to make it shorter. Your experience and creativity will have to come in play.
Should not have
• should not have other colors beside logo color and black text (2 colors). Also nothing Three dimensional

```html
<!DOCTYPE html>
<html lang="en">
<head>
<meta charset="utf-8">
<title>Ridgeline Press — Business Card</title>
<link rel="stylesheet" href="https://fonts.googleapis.com/css2?family=Source+Sans+3:wght@400;600;700&display=swap">
<style>
  :root {
    --brand-blue: #1f7bc1;
    --ink: #111111;
    --paper: #ffffff;
    --backdrop: #ecebe8;
  }
  * { box-sizing: border-box; margin: 0; padding: 0; }
  html, body { width: 1200px; height: 900px; overflow: hidden; }
  body {
    position: relative;
    background: var(--backdrop);
    font-family: "Source Sans 3", "Myriad Pro", Arial, sans-serif;
  }
  .card { position: absolute; width: 585px; height: 378px; }

  /* Front side */
  .card-front { left: 93px; top: 48px; background: var(--paper); }
  .front-mark {
    position: absolute; left: 268px; top: 62px;
    width: 50px; height: 50px; border-radius: 50%;
    background: var(--brand-blue);
  }
  .front-company {
    position: absolute; left: 0; right: 0; top: 128px;
    text-align: center; font-weight: 600; font-size: 21px;
    color: var(--ink); letter-spacing: -0.2px;
  }
  .front-slogan {
    position: absolute; left: 0; right: 0; top: 158px;
    text-align: center; font-size: 17px; color: var(--brand-blue);
  }
  .contact-band {
    position: absolute; left: 0; right: 0; top: 208px; height: 132px;
    background: var(--brand-blue); color: var(--paper);
  }
  .person { position: absolute; right: 350px; top: 24px; text-align: right; }
  .person-name { font-weight: 600; font-size: 19px; line-height: 24px; }
  .person-title { font-weight: 600; font-size: 15px; line-height: 22px; }
  .band-divider {
    position: absolute; left: 276px; top: 20px; width: 3px; height: 96px;
    background: linear-gradient(to bottom, rgba(255,255,255,0), #ffffff 50%, rgba(255,255,255,0));
  }
  .contact-list { position: absolute; left: 310px; top: 20px; list-style: none; font-size: 14.5px; line-height: 18px; }
  .contact-list li { position: relative; padding-left: 24px; margin-bottom: 7px; }
  .contact-list svg { position: absolute; left: 0; top: 2px; width: 14px; height: 14px; fill: var(--paper); }
  .front-url {
    position: absolute; left: 0; right: 0; top: 347px;
    text-align: center; font-size: 15px; color: var(--brand-blue);
  }

  /* Back side */
  .card-back { left: 472px; top: 450px; width: 586px; height: 380px; background: var(--brand-blue); color: var(--paper); }
  .back-mark {
    position: absolute; left: 258px; top: 86px;
    width: 70px; height: 70px; border-radius: 50%;
    background: var(--paper);
  }
  .back-company {
    position: absolute; left: 0; right: 0; top: 188px;
    text-align: center; font-weight: 600; font-size: 27px; letter-spacing: -0.2px;
  }
  .back-slogan { position: absolute; left: 0; right: 0; top: 230px; text-align: center; font-size: 18px; }
  .back-url { position: absolute; left: 0; right: 0; top: 335px; text-align: center; font-size: 16px; }
</style>
</head>
<body>
  <section class="card card-front" aria-label="Business card front">
    <div class="front-mark" aria-hidden="true"></div>
    <h1 class="front-company">TAMARIND RIDGELINE MEDIA</h1>
    <p class="front-slogan">Your information gateway</p>
    <div class="contact-band">
      <div class="person">
        <p class="person-name">OWEN FARSK</p>
        <p class="person-title">Director of Sales &amp; Marketing</p>
      </div>
      <div class="band-divider"></div>
      <ul class="contact-list">
        <li>
          <svg viewBox="0 0 16 16" aria-hidden="true"><path d="M8 1 0 8h2v7h4.5v-4.5h3V15H14V8h2z"/></svg>
          #2714 - 582 E. Halvern St.<br>Vancouver, B.C. V7K2R4 Canada
        </li>
        <li>
          <svg viewBox="0 0 16 16" aria-hidden="true"><path d="M3.6 1 6 4.2 4.6 6c.9 2 2.5 3.6 4.4 4.5L10.8 9 14 11.4 12.5 14C6.8 13.6 2.4 9.2 2 3.5z"/></svg>
          604 317 8842
        </li>
        <li>
          <svg viewBox="0 0 16 16" aria-hidden="true"><path d="M1 4h14v9H1z" fill="none" stroke="#fff" stroke-width="1.4"/><path d="M1 4l7 5 7-5" fill="none" stroke="#fff" stroke-width="1.4"/></svg>
          owen@tamarindridgeline.biz
        </li>
      </ul>
    </div>
    <p class="front-url">www.tamarindridgeline.biz</p>
  </section>

  <section class="card card-back" aria-label="Business card back">
    <div class="back-mark" aria-hidden="true"></div>
    <h2 class="back-company">TAMARIND RIDGELINE MEDIA</h2>
    <p class="back-slogan">Your information gateway</p>
    <p class="back-url">www.tamarindridgeline.biz</p>
  </section>
</body>
</html>
```